Website Design for Forklift Training Company

DO NOT CONTACT PRIVATELY. ONLY SUBMISSIONS HERE WILL BE CONSIDERED

I need a design for a website that offers forklift training courses.

The company offers accredited, onsite forklift training that are customized for the needs of each individual company. The company offers a variety of courses to operate forklifts and other machinary.

About: "KVW Training Ltd delivers bespoke onsite forklift truck operator training throught the uk.
All our instructors have a wealth of knowledge and expertise to provide your company with all your forklift truck training requirements.
KVW Training Ltd is registered and accredited by plomvex standards so you can be rest assured that all forklift training is carried out the very highest standard"

I need the following pages designed:
> a) Home Page: Include a header image, ways to contact, about snippet, overview of courses, accreditation that will be received after completing the courses. (See attachments for samples)
> b) About Page
> c) Contact Us Page
> d) Course Page Template: A page that will be used as template for the courses offered. It should contain;
1. Cover image for the course
2. A description of the course
3. A table indicating the various course options
4. Course Objectives
5. What the trainee will receive after doing the course (example: a certification)

Industrial Businesses

4 page

Colors
0054AA
0677BA
7BADD7
CADEEF
E8F1F8
0094D4
00A9DD
6FCCEA
C7EBF8
E9F6FB

• - No Search bar

```html
<!DOCTYPE html>
<html lang="en">
<head>
<meta charset="utf-8">
<title>KVW Training Ltd – About</title>
<link href="https://fonts.googleapis.com/css2?family=Montserrat:wght@400;600;700;800&family=Open+Sans:wght@400;600&family=Oswald:wght@500&display=swap" rel="stylesheet">
<style>
:root{
  --navy:#0054AA;
  --blue:#0677BA;
  --sky:#0094D4;
  --cyan:#00A9DD;
  --soft:#7BADD7;
  --pale:#CADEEF;
  --mist:#E8F1F8;
  --ice:#E9F6FB;
  --ink:#1d2a3a;
  --grey:#5d6b7a;
  --white:#ffffff;
  --deep:#063f82;
}
*{box-sizing:border-box;margin:0;padding:0}
html,body{width:1200px;height:3320px;overflow:hidden}
body{position:relative;background:var(--white);font-family:"Open Sans",Arial,sans-serif;color:var(--ink)}
.abs{position:absolute}

/* hero */
.hero{left:0;top:0;width:1200px;height:520px;background:linear-gradient(120deg,var(--navy),var(--blue) 70%);overflow:hidden}
.hero-photo{left:0;top:0;width:1200px;height:520px}
.brand{left:60px;top:22px;display:flex;align-items:center;gap:12px;color:var(--white);font-family:"Montserrat",sans-serif;font-weight:700;font-size:17px;letter-spacing:.5px}
.brand-mark{width:26px;height:26px;border:3px solid var(--white)}
.nav{top:22px;left:310px;display:flex;gap:58px}
.nav a{color:var(--white);text-decoration:none;font-family:"Montserrat",sans-serif;font-weight:600;font-size:15px}
.hero-kicker{left:80px;top:170px;color:var(--white);font-family:"Montserrat",sans-serif;font-weight:600;font-size:26px;letter-spacing:1px}
.hero-title{left:80px;top:208px;color:var(--white);font-family:"Montserrat",sans-serif;font-weight:800;font-size:46px;letter-spacing:1px}

/* about */
.about-head{top:580px;left:0;width:1200px;text-align:center}
.about-head small{display:block;font-family:"Montserrat",sans-serif;font-weight:600;font-size:22px;color:var(--blue)}
.about-head h2{font-family:"Montserrat",sans-serif;font-weight:800;font-size:42px;color:var(--navy)}
.about-head h2 span{color:var(--cyan)}
.about-rule{left:560px;top:676px;width:80px;height:4px;background:var(--sky)}
.about-text{left:240px;top:700px;width:720px;text-align:center;font-size:15px;line-height:24px;color:var(--grey)}
.diagram{left:200px;top:800px;width:800px;height:520px}
.tag{font-family:"Montserrat",sans-serif;font-weight:700;font-size:14px;color:var(--blue);width:170px}
.tag p{font-family:"Open Sans",sans-serif;font-weight:400;font-size:11px;line-height:15px;color:var(--grey);margin-top:4px}
.tag.right{text-align:right}

/* mission */
.mission{left:0;top:1340px;width:1200px;height:580px;background:var(--mist)}
.mission-photo{left:112px;top:1420px;width:508px;height:440px;background:linear-gradient(135deg,#8a6a3a,#c59a4a 40%,#5a86b4)}
.mission-card{left:540px;top:1480px;width:540px;height:320px;background:var(--white);box-shadow:0 14px 34px rgba(6,63,130,.18);padding:44px 40px}
.mission-card h3{font-family:"Montserrat",sans-serif;font-weight:800;font-size:30px;color:var(--navy)}
.mission-card h3 span{color:var(--sky)}
.mission-card .rule{width:60px;height:4px;background:var(--sky);margin:10px 0 20px}
.mission-card p{font-size:15px;line-height:24px;color:var(--grey)}
.mission-edge{left:1080px;top:1500px;width:14px;height:300px;background:var(--navy)}

/* vehicles */
.vehicles{left:0;top:1920px;width:1200px;height:600px;background:linear-gradient(180deg,var(--navy),var(--blue))}
.vehicles-title{top:2012px;left:0;width:1200px;text-align:center;color:var(--white);font-family:"Montserrat",sans-serif;font-weight:800;font-size:38px}
.vehicles-rule{left:560px;top:2066px;width:80px;height:4px;background:var(--soft)}
.card{top:2100px;width:240px;height:340px;background:var(--white);border-radius:10px;overflow:hidden;text-align:center}
.card .shot{height:170px;margin:16px;border-radius:6px;background:linear-gradient(160deg,#f4f4f4,#d9dde2)}
.card h4{font-family:"Oswald",sans-serif;font-weight:500;font-size:19px;color:var(--ink);letter-spacing:.3px;padding:0 10px;white-space:nowrap}
.card p{font-size:12px;line-height:17px;color:var(--grey);padding:8px 22px 0}

/* benefits */
.benefits{left:0;top:2520px;width:1200px;height:620px;background:var(--ice)}
.benefits-box{left:140px;top:2620px;width:300px;height:440px;background:linear-gradient(160deg,var(--sky),var(--navy));padding:54px 34px;text-align:right;color:var(--white)}
.benefits-box small{display:block;font-family:"Montserrat",sans-serif;font-weight:600;font-size:18px}
.benefits-box h3{font-family:"Montserrat",sans-serif;font-weight:800;font-size:32px;line-height:38px}
.benefits-photo{left:120px;top:2820px;width:240px;height:260px;background:linear-gradient(160deg,#f0cf5a,#c8a12a 60%,#3b3f46)}
.benefits-card{left:440px;top:2640px;width:660px;height:300px;background:var(--white);box-shadow:0 14px 34px rgba(6,63,130,.15);padding:40px 48px}
.benefits-card > p{font-size:15px;line-height:24px;color:var(--grey)}
.benefits-card .sep{height:1px;background:var(--pale);margin:22px 0}
.points{display:flex;gap:36px}
.point{width:170px;text-align:center;font-size:11px;line-height:15px;color:var(--grey)}
.point svg{display:block;margin:0 auto 10px}
.benefits-bar{left:440px;top:2940px;width:660px;height:8px;background:var(--navy)}

/* footer */
.footer{left:0;top:3140px;width:1200px;height:180px;background:var(--deep);text-align:center;color:var(--white)}
.footer-nav{display:flex;justify-content:center;gap:90px;margin-top:54px}
.footer-nav a{color:var(--white);text-decoration:none;font-family:"Montserrat",sans-serif;font-weight:600;font-size:15px}
.footer small{display:block;margin-top:18px;font-size:11px;color:var(--pale);letter-spacing:.5px}
.social{display:flex;justify-content:center;gap:10px;margin-top:12px}
.social span{width:22px;height:22px;border-radius:50%;background:var(--white)}
</style>
</head>
<body>

<section class="hero abs">
  <svg class="hero-photo abs" viewBox="0 0 1200 520" role="img" aria-label="Photo of an instructor operating a yellow forklift in a warehouse">
    <defs>
      <linearGradient id="heroShot" x1="0" y1="0" x2="1" y2="1">
        <stop offset="0" stop-color="#9fb7cf"/>
        <stop offset=".55" stop-color="#c9b167"/>
        <stop offset="1" stop-color="#5c6a78"/>
      </linearGradient>
    </defs>
    <path d="M0 470 C300 420 560 380 740 250 L740 520 L0 520 Z" fill="#ffffff" opacity=".06"/>
    <path d="M900 0 C820 130 800 330 740 520 L1200 520 L1200 0 Z" fill="url(#heroShot)"/>
    <path d="M900 0 C820 130 800 330 740 520" fill="none" stroke="#ffffff" stroke-width="6"/>
    <path d="M0 520 C320 500 600 430 760 470 C900 500 1050 520 1200 500 L1200 520 Z" fill="#ffffff"/>
  </svg>
  <div class="brand abs"><span class="brand-mark"></span>KVW TRAINING LTD</div>
  <nav class="nav abs"><a>HOME</a><a>ABOUT US</a><a>COURSES</a><a>CONTACT US</a></nav>
  <div class="hero-kicker abs">WHO WE ARE</div>
  <h1 class="hero-title abs">ABOUT KVW TRAINING</h1>
</section>

<div class="about-head abs"><small>WHO WE ARE</small><h2>ABOUT <span>KVW TRAINING</span></h2></div>
<div class="about-rule abs"></div>
<p class="about-text abs">KVW Training Ltd delivers bespoke onsite forklift truck operator training throughout the UK. All our instructors have a wealth of knowledge and expertise to provide your company with all your forklift truck training requirements. KVW Training Ltd is registered and accredited by plomvex standards so you can be rest assured that all forklift training is carried out to the very highest standard.</p>

<svg class="diagram abs" viewBox="0 0 800 520">
  <defs>
    <linearGradient id="hub" x1="0" y1="0" x2="0" y2="1">
      <stop offset="0" stop-color="#0094D4"/><stop offset="1" stop-color="#0054AA"/>
    </linearGradient>
  </defs>
  <path d="M210 330 A190 190 0 1 1 590 330" fill="none" stroke="#7BADD7" stroke-width="3"/>
  <circle cx="400" cy="300" r="160" fill="url(#hub)"/>
  <rect x="300" y="180" width="200" height="240" rx="8" fill="#e6c14a" opacity=".9" role="img" aria-label="Photo of a yellow forklift truck"/>
  <ellipse cx="400" cy="470" rx="190" ry="16" fill="#CADEEF"/>
  <g fill="#0677BA">
    <circle cx="400" cy="110" r="7"/>
    <circle cx="250" cy="175" r="7"/>
    <circle cx="550" cy="175" r="7"/>
    <circle cx="215" cy="270" r="7"/>
    <circle cx="585" cy="270" r="7"/>
  </g>
</svg>
<div class="tag abs" style="left:614px;top:812px">FORKLIFT TRAINING<p>Short course for safe truck use on site.</p></div>
<div class="tag right abs" style="left:360px;top:878px">MULTILANE<p>Short course for safe truck use on site.</p></div>
<div class="tag abs" style="left:770px;top:878px">KRANVO TRAINING<p>Short course for safe truck use on site.</p></div>
<div class="tag right abs" style="left:220px;top:1010px">OTHER TRAINING<p>Short course for safe truck use on site.</p></div>
<div class="tag abs" style="left:805px;top:1010px">OTHER TRAINING<p>Short course for safe truck use on site.</p></div>

<section class="mission abs"></section>
<div class="mission-photo abs" role="img" aria-label="Photo of a trainee in a hard hat seated on a forklift"></div>
<div class="mission-edge abs"></div>
<div class="mission-card abs">
  <h3>OUR <span>MISSION</span></h3>
  <div class="rule"></div>
  <p>Lorem Ipsum is simply dummy text of the printing and typesetting industry. Lorem Ipsum has been the industry's standard dummy text ever since the 1500s, when an unknown printer took a galley of type and scrambled it to make a type specimen book. It has survived not only five centuries, but also the leap into electronic typesetting, remaining essentially.</p>
</div>

<section class="vehicles abs"></section>
<h2 class="vehicles-title abs">OUR VECHICLES</h2>
<div class="vehicles-rule abs"></div>
<article class="card abs" style="left:72px"><div class="shot" role="img" aria-label="Photo of a compact skid steer loader"></div><h4>SKIDMOOR TRAINING</h4><p>Skid steers are essential in the workplace and are thought useful in warehouses.</p></article>
<article class="card abs" style="left:328px"><div class="shot" role="img" aria-label="Photo of a yellow cherry picker"></div><h4>CHERRY PICKER TRAINING</h4><p>The Work at Height Regulations 2005 require that works be planned competently.</p></article>
<article class="card abs" style="left:584px"><div class="shot" role="img" aria-label="Photo of a multidirectional lift truck"></div><h4>MULTILANE TRAINING</h4><p>Multi-way forklifts are essential in the workplace and are used through the world.</p></article>
<article class="card abs" style="left:840px"><div class="shot" role="img" aria-label="Photo of an articulated flexi forklift"></div><h4>FLEXI TRAINING</h4><p>Flexis are essential in the workplace and are thought useful in warehouses.</p></article>

<section class="benefits abs"></section>
<div class="benefits-box abs"><small>OUR BENEFITS</small><h3>WHY CHOOSE US</h3></div>
<div class="benefits-photo abs" role="img" aria-label="Photo of a yellow forklift truck"></div>
<div class="benefits-card abs">
  <p>Standard dummy text ever since the 1500s, when an unknown printer took a galley of type and scrambled it to make a type specimen book. It has survived not only five centuries, but also the leap.</p>
  <div class="sep"></div>
  <div class="points">
    <div class="point"><svg width="40" height="40" viewBox="0 0 40 40"><circle cx="20" cy="20" r="18" fill="none" stroke="#0677BA" stroke-width="2"/><path d="M12 20l6 6 10-12" fill="none" stroke="#0677BA" stroke-width="2.5"/></svg>Accredited trainers on site with years of practice.</div>
    <div class="point"><svg width="40" height="40" viewBox="0 0 40 40"><circle cx="20" cy="20" r="18" fill="none" stroke="#0677BA" stroke-width="2"/><path d="M20 10v10l7 5" fill="none" stroke="#0677BA" stroke-width="2.5"/></svg>Flexible course times to suit your business.</div>
    <div class="point"><svg width="40" height="40" viewBox="0 0 40 40"><circle cx="20" cy="20" r="18" fill="none" stroke="#0677BA" stroke-width="2"/><path d="M13 14h14v12H13z M17 30h6" fill="none" stroke="#0677BA" stroke-width="2.5"/></svg>Certificates issued to every trainee who passes.</div>
  </div>
</div>
<div class="benefits-bar abs"></div>

<footer class="footer abs">
  <nav class="footer-nav"><a>HOME</a><a>ABOUT US</a><a>COURSES</a><a>CONTACT US</a></nav>
  <small>© 2024 COPYRIGHT KVW TRAINING LTD. ALL RIGHTS RESERVED.</small>
  <div class="social"><span></span><span></span><span></span></div>
</footer>

</body>
</html>
```